Accounting firm needing business card / letterhead designed
Marcus L. Trenholm, CPA
marcus@veltrowledger.com
www.veltrowledger.com
842 E Alder Ave Corvane, OH 43827
555-562-0974

```html
<!DOCTYPE html>
<html lang="en">
<head>
<meta charset="utf-8">
<title>Veltrow Ledger — Stationery</title>
<link href="https://fonts.googleapis.com/css2?family=Lato:wght@400;700&family=Roboto:wght@400;500&display=swap" rel="stylesheet">
<style>
  :root {
    --navy: #262262;
    --green: #8dc63f;
    --ink: #6d6d6d;
    --text-dark: #444444;
    --paper: #ffffff;
    --backdrop: #e6e6e6;
  }
  * { box-sizing: border-box; margin: 0; padding: 0; }
  html, body { width: 1200px; height: 984px; overflow: hidden; }
  body {
    background: var(--backdrop);
    font-family: "Lato", sans-serif;
    color: var(--ink);
    position: relative;
  }

  .brand {
    font-family: "Lato", sans-serif; font-weight: 700;
    color: var(--navy); text-transform: uppercase;
    letter-spacing: 1px; line-height: 1; white-space: nowrap;
  }

  .contact-line { display: flex; align-items: center; gap: 6px; }
  .contact-line svg { width: 8px; height: 8px; fill: var(--navy); flex: none; }

  .band { position: absolute; left: 0; width: 100%; }
  .band svg { display: block; width: 100%; height: 100%; }
  .band-url {
    position: absolute; top: 0; left: 0; height: 100%;
    display: flex; align-items: center; color: #fff;
  }

  /* Letterhead */
  .letterhead {
    position: absolute; left: 97px; top: 106px;
    width: 554px; height: 778px; background: var(--paper);
    box-shadow: 0 4px 14px rgba(0,0,0,.18);
  }
  .letterhead .brand { position: absolute; left: 49px; top: 68px; font-size: 20px; }
  .letterhead .sender {
    position: absolute; left: 396px; top: 51px; font-size: 8.5px; line-height: 12px; color: var(--text-dark);
  }
  .letterhead .sender address { font-style: normal; margin-bottom: 4px; }
  .letterhead .sender .contact-line { margin-top: 2px; }
  .recipient { position: absolute; left: 49px; top: 223px; font-size: 10px; line-height: 14.5px; }
  .letter-body { position: absolute; left: 49px; top: 304px; width: 459px; font-size: 9.8px; line-height: 14.5px; text-align: justify; }
  .letter-body p + p { margin-top: 29px; }
  .signature { position: absolute; left: 48px; top: 508px; width: 105px; height: 70px; background: linear-gradient(135deg, #ecebf5, #dcdbee); }
  .sign-title { position: absolute; left: 48px; top: 599px; font-size: 10px; }
  .letterhead .band { bottom: 22px; height: 22px; }
  .letterhead .band-url { left: 51px; font-size: 9.5px; }

  /* Business cards */
  .card {
    position: absolute; left: 709px; width: 380px; height: 217px;
    box-shadow: 0 4px 14px rgba(0,0,0,.18);
  }
  .card-front { top: 251px; background: var(--paper); }
  .card-front .brand { position: absolute; left: 25px; top: 36px; font-size: 19px; }
  .holder { position: absolute; left: 25px; top: 102px; font-family: "Roboto", sans-serif; }
  .holder-name { font-size: 16px; font-weight: 500; color: var(--navy); line-height: 20px; }
  .holder-role { font-size: 11px; color: var(--text-dark); margin-top: 2px; }
  .card-front .contacts { position: absolute; left: 25px; top: 148px; font-size: 8.5px; line-height: 13px; color: var(--text-dark); }
  .card-front address {
    position: absolute; right: 22px; top: 150px; font-style: normal; text-align: right;
    font-size: 8.5px; line-height: 12px; color: var(--text-dark);
  }
  .card-front .band { top: 185px; height: 16px; }
  .card-front .band-url { left: 26px; font-size: 8.5px; }

  .card-back { top: 510px; background: var(--navy); color: #fff; }
  .card-back .brand { position: absolute; left: 0; right: 0; top: 96px; text-align: center; color: #fff; font-size: 22px; }
  .card-back .back-url { position: absolute; left: 0; right: 0; top: 183px; text-align: center; font-size: 9.5px; }
</style>
</head>
<body>

<svg width="0" height="0" style="position:absolute" aria-hidden="true">
  <symbol id="icon-phone" viewBox="0 0 24 24"><path d="M6.6 10.8a15.1 15.1 0 0 0 6.6 6.6l2.2-2.2c.3-.3.7-.4 1-.2 1.1.4 2.3.6 3.6.6.6 0 1 .4 1 1V20c0 .6-.4 1-1 1A17 17 0 0 1 3 4c0-.6.4-1 1-1h3.5c.6 0 1 .4 1 1 0 1.3.2 2.5.6 3.6.1.3 0 .7-.2 1z"/></symbol>
  <symbol id="icon-mail" viewBox="0 0 24 24"><path d="M2 5h20v2l-10 6L2 7z M2 9l10 6 10-6v10H2z"/></symbol>
</svg>

<article class="letterhead">
  <div class="brand">Veltrow Ledger</div>
  <div class="sender">
    <address>842 E Alder Ave Corvane<br>OH 43827</address>
    <div class="contact-line"><svg><use href="#icon-phone"/></svg>555-562-0974</div>
    <div class="contact-line"><svg><use href="#icon-mail"/></svg>marcus@veltrowledger.com</div>
  </div>

  <div class="recipient">Dear Halvorsen<br>Brindle Crest Corporation<br>Department Design</div>

  <div class="letter-body">
    <p>Lorem ipsum dolor sit amet, consectetuer adipiscing elit. Aenean commodo ligula eget dolor. Aenean massa. Cum sociis natoque penatibus et magnis dis parturient montes, nascetur ridiculus mus. Donec quam felis, ultricies nec, pellentesque eu, pretium quis, sem. Nulla consequat massa quis enim. Donec pede justo, fringilla vel, aliquet nec, vulputate eget, arcu. In enim justo, rhoncus ut, imperdiet a, venenatis vitae, justo. Nullam dictum felis eu pede mollis pretium. Integer tincidunt. Cras dapibus. Vivamus elementum semper nisi.Nullam dictum felis eu pede mollis pretium. Integer tincidunt. Cras dapibus. Vivamus elementum semper nisi.felis eu pede mollis pretium. Integer tincidunt. Cras dapibus.</p>
    <p>Quisque rutrum. Aenean imperdiet. Etiam ultricies nisi vel augue. Curabitur ullamcorper ultricies nisi. Nam eget dui. Etiam rhoncus. Maecenas tempus, tellus eget condimentum rhoncus, sem quam semper libero, sit amet adipiscing sem neque sed ipsum.felis pede mollis pretium. I am tincidunt. Cras dapibus.</p>
  </div>

  <div class="signature" role="img" aria-label="Handwritten signature of the director"></div>
  <div class="sign-title">Director/Excecutive Director</div>

  <div class="band">
    <svg viewBox="0 0 554 22" preserveAspectRatio="none" aria-hidden="true">
      <polygon points="0,0 380,0 372,22 0,22" fill="var(--navy)"/>
      <polygon points="384,0 554,0 554,22 376,22" fill="var(--green)"/>
    </svg>
    <span class="band-url">www.veltrowledger.com</span>
  </div>
</article>

<article class="card card-front">
  <div class="brand">Veltrow Ledger</div>
  <div class="holder">
    <div class="holder-name">Marcus L. Trenholm</div>
    <div class="holder-role">CPA</div>
  </div>
  <div class="contacts">
    <div class="contact-line"><svg><use href="#icon-phone"/></svg>555-562-0974</div>
    <div class="contact-line"><svg><use href="#icon-mail"/></svg>marcus@veltrowledger.com</div>
  </div>
  <address>842 E Alder Ave Corvane<br>OH 43827</address>
  <div class="band">
    <svg viewBox="0 0 380 16" preserveAspectRatio="none" aria-hidden="true">
      <polygon points="0,0 248,0 242,16 0,16" fill="var(--navy)"/>
      <polygon points="252,0 380,0 380,16 246,16" fill="var(--green)"/>
    </svg>
    <span class="band-url">www.veltrowledger.com</span>
  </div>
</article>

<article class="card card-back">
  <div class="brand">Veltrow Ledger</div>
  <div class="back-url">www.veltrowledger.com</div>
</article>

</body>
</html>
```